Website for new dental office

I am Dr. Colin Ashford and am building a new dental practice. I specialize in general dentistry. I am young and have a higher end dental practice incorporating very new technologies and would like my website to reflect that. As many dental patients are older, the website must be very easy to navigate. I would like patients to be able to request appointments, and will eventually add on patient information forms (the health history, etc, that you normally fill out in the practice) from my practice management software, so leave an area for that.

Industry/Entity Type

Building

```html
<!DOCTYPE html>
<html lang="en">
<head>
<meta charset="utf-8">
<title>Colin Ashford, DDS</title>
<link href="https://fonts.googleapis.com/css2?family=Open+Sans:wght@400;600;700&family=Montserrat:wght@400;500;600&family=Raleway:wght@400;500&display=swap" rel="stylesheet">
<style>
:root{
  --orange:#e8922a;
  --orange-dark:#d97d14;
  --ink:#2b2b2b;
  --text:#555;
  --muted:#8a8a8a;
  --nav:#1f1f1f;
  --field:#e8e8e8;
  --page:#f2f2f2;
  --line:#e2e2e2;
}
*{box-sizing:border-box;margin:0;padding:0}
html,body{width:847px;height:1200px;overflow:hidden}
body{position:relative;background:var(--page);font-family:"Open Sans",sans-serif;color:var(--text)}
.abs{position:absolute}
.top-rule{left:0;top:0;width:847px;height:3px;background:var(--orange)}
.cta-consult{left:580px;top:0;width:198px;height:28px;background:var(--orange);color:#fff;font:400 13px "Open Sans",sans-serif;display:flex;align-items:center;justify-content:center}
.cta-consult b{margin:0 3px}
.brand{left:74px;top:34px;font:600 21px "Open Sans",sans-serif;color:var(--ink);letter-spacing:.3px}
.phone{left:617px;top:42px;display:flex;align-items:center;gap:6px;font:400 19px "Open Sans",sans-serif;color:var(--ink)}
.nav{left:0;top:82px;width:847px;height:34px;background:linear-gradient(#2e2e2e,#151515)}
.nav a{position:absolute;top:0;height:34px;line-height:34px;color:#fff;font-size:10px;text-decoration:none;transform:translateX(-50%)}
.nav a.active{left:95px;width:52px;background:var(--orange);text-align:center;font-weight:700;border-top:2px solid #f5b25c;line-height:31px}
.hero{left:0;top:116px;width:847px;height:280px;background:linear-gradient(90deg,#f4f4f4 0%,#e9e9e9 55%,#dedede 100%)}
.hero-photo{left:448px;top:116px;width:399px;height:280px;background:linear-gradient(90deg,rgba(230,230,230,0) 0%,#d9dde0 35%,#c9d2d8 70%,#dfe4e7 100%)}
.hero h1{left:72px;top:210px;font:500 30px "Montserrat",sans-serif;color:#333;letter-spacing:-.6px}
.hero h1 span,.hl{color:var(--orange)}
.hero-sub{left:72px;top:246px;font:400 20px "Raleway",sans-serif;color:#333;letter-spacing:.8px}
.btn-more{left:74px;top:286px;width:112px;height:30px;background:var(--orange);color:#2b2b2b;font:500 11px "Open Sans",sans-serif;display:flex;align-items:center;padding-left:11px;gap:10px}
.panel{left:78px;top:412px;width:692px;height:572px;background:#fff;border:1px solid #e6e6e6}
.panel-band{left:78px;top:412px;width:692px;height:190px;background:linear-gradient(#f6f6f6,#dedede)}
.arrow-circle{width:26px;height:26px;border-radius:50%;background:#fff;border:2px solid #d5d5d5;display:flex;align-items:center;justify-content:center}
.about-title{left:97px;top:430px;font:700 18px "Open Sans",sans-serif;color:#2b2b2b}
.about-text{left:97px;top:463px;width:160px;font-size:9px;line-height:14.8px;color:#888}
.svc-img{top:430px;width:146px;height:78px}
.svc-title{top:517px;font:600 12px "Open Sans",sans-serif;color:#333}
.svc-text{top:538px;width:140px;font-size:8.6px;line-height:13.6px;color:#8f8f8f}
.welcome{left:94px;top:632px;font:400 16px "Montserrat",sans-serif;color:var(--orange)}
.welcome-img{left:94px;top:660px;width:177px;height:93px;background:linear-gradient(90deg,#c9b2a8,#e6ecee 55%,#9fc9d4)}
.welcome-text{left:279px;top:664px;width:218px;font-size:8.5px;line-height:12.8px;color:#555;letter-spacing:.2px}
.divider{left:94px;top:775px;width:400px;height:1px;background:var(--line)}
.vdivider{left:522px;top:632px;width:1px;height:340px;background:var(--line)}
.appt-title{left:94px;top:795px;font:400 17px "Montserrat",sans-serif;color:#333;letter-spacing:-.3px}
.field{background:var(--field);font-size:9px;color:#666;padding:6px 8px;border:1px solid #e2e2e2}
.btn-send{left:97px;top:926px;width:80px;height:26px;background:linear-gradient(#f4a339,var(--orange-dark));color:#fff;font:700 11px "Open Sans",sans-serif;letter-spacing:.5px;display:flex;align-items:center;justify-content:center}
.stories-title{left:539px;top:632px;font:500 17px "Montserrat",sans-serif;color:#2b2b2b;letter-spacing:-.3px}
.story{left:539px;width:230px;height:62px}
.story-img{position:absolute;left:0;top:0;width:57px;height:60px;background:linear-gradient(135deg,#d9c3b0,#b89a85 60%,#e4e4e4)}
.story h3{position:absolute;left:63px;top:-2px;font:600 10px "Open Sans",sans-serif;color:#333}
.story p{position:absolute;left:63px;top:15px;width:160px;font-size:7.4px;line-height:10.6px;color:#444}
.story .more{position:absolute;left:63px;top:52px;font-size:7.4px;font-style:italic;color:#999}
.foot-h{top:1008px;font:400 13px "Open Sans",sans-serif;color:#444}
.foot-list{top:1040px;list-style:none;font-size:10px;line-height:15.6px;color:#666}
.foot-list li::before{content:"• ";color:#999}
.foot-brand{left:582px;top:1002px;font:600 17px "Open Sans",sans-serif;color:var(--ink)}
.foot-addr{left:589px;top:1040px;font-size:10px;line-height:15.6px;color:#666}
.foot-rule{left:78px;top:1163px;width:692px;height:1px;background:#dcdcdc}
.copy{left:0;top:1174px;width:847px;text-align:center;font-size:9px;color:#333}
</style>
</head>
<body>
<div class="abs top-rule"></div>
<div class="abs cta-consult">Request a <b>FREE</b> Consultation</div>
<div class="abs brand">Colin Ashford, DDS</div>
<div class="abs phone">
  <svg width="22" height="20" viewBox="0 0 22 20"><path d="M5 3c1-1 2-1 3 0l2 3c.5 1 0 2-1 2.5 1 2 2.5 3.5 4.5 4.5.5-1 1.5-1.5 2.5-1l3 2c1 1 1 2 0 3l-1.5 1.5C13 19 3 9 3.5 4.5z" fill="#333"/><circle cx="14" cy="5" r="4" fill="none" stroke="#333" stroke-width="1.5"/></svg>
  (123) 555-0148
</div>

<nav class="abs nav">
  <a class="active" href="#">HOME</a>
  <a href="#" style="left:172px">About Us</a>
  <a href="#" style="left:262px">philosophy</a>
  <a href="#" style="left:356px">Restorative</a>
  <a href="#" style="left:446px">Cosmetic</a>
  <a href="#" style="left:555px">Tooth Replacement</a>
  <a href="#" style="left:666px">Patient Info</a>
  <a href="#" style="left:752px">Contact</a>
</nav>

<section>
  <div class="abs hero"></div>
  <div class="abs hero-photo" role="img" aria-label="Smiling dentist in a white coat in a modern treatment room"></div>
  <div class="hero"><h1 class="abs">I specialize in <span>General Dentistry</span></h1></div>
  <div class="abs hero-sub">Teeth Whitening Solutions for Everyone</div>
  <div class="abs btn-more">READ MORE
    <svg width="22" height="22" viewBox="0 0 22 22"><circle cx="11" cy="11" r="10" fill="#f3f3f3"/><path d="M6 9.5h6V6l5 5-5 5v-3.5H6z" fill="#777"/></svg>
  </div>
</section>

<div class="abs panel"></div>
<div class="abs panel-band"></div>
<div class="abs arrow-circle" style="left:64px;top:495px"><svg width="8" height="8" viewBox="0 0 8 8"><path d="M6 0v8L1 4z" fill="#aaa"/></svg></div>
<div class="abs arrow-circle" style="left:757px;top:495px"><svg width="8" height="8" viewBox="0 0 8 8"><path d="M2 0v8l5-4z" fill="#aaa"/></svg></div>

<div class="abs about-title">ABOUT US</div>
<p class="abs about-text">It is a long established fact that a reader will be distracted by the readable content of a page when looking at its layout. The point of using Lorem Ipsum is that it has a more-or-less normal distribution of letters, as opposed to using 'Content here, content here.</p>

<div class="abs svc-img" style="left:279px;background:linear-gradient(#f2d8cc,#c94b3e 55%,#f0dcd2)" role="img" aria-label="Close-up of a bright white smile"></div>
<div class="abs svc-img" style="left:438px;background:linear-gradient(120deg,#e8cfc4,#c98c80 55%,#e9e3df)" role="img" aria-label="Dentist examining a patient's teeth with a mirror"></div>
<div class="abs svc-img" style="left:596px;background:linear-gradient(90deg,#c8a591,#d9bba8 60%,#3fa1a3)" role="img" aria-label="Patient smiling during tooth replacement care"></div>

<div class="abs svc-title" style="left:281px">Cosmetics</div>
<div class="abs svc-title" style="left:444px">Restorative</div>
<div class="abs svc-title" style="left:597px">Tooth replacement</div>
<p class="abs svc-text" style="left:281px">It is a long established fact that a reader will be distracted by the readable content of a page when looking at its layout.</p>
<p class="abs svc-text" style="left:444px">It is a long established fact that a reader will be distracted by the readable content of a page when looking at its layout.</p>
<p class="abs svc-text" style="left:596px">It is a long established fact that a reader will be distracted by the readable content of a page when looking at its layout.</p>

<h2 class="abs welcome">Welcome to Colin Ashford, DDS</h2>
<div class="abs welcome-img" role="img" aria-label="Dentist treating a smiling patient"></div>
<p class="abs welcome-text">It is a long established fact that a reader will be distracted by the readable content of a page when looking at its layout. The point of using Lorem Ipsum is that it has a more-or-less normal distribution of letters, as opposed to using 'Content here, content here', making it look like readable English.</p>
<div class="abs divider"></div>
<div class="abs vdivider"></div>

<h2 class="abs appt-title">Request an Appointment</h2>
<div class="abs field" style="left:96px;top:832px;width:173px;height:23px">Name*</div>
<div class="abs field" style="left:280px;top:832px;width:173px;height:23px">Phone*</div>
<div class="abs field" style="left:96px;top:862px;width:173px;height:23px">Email*</div>
<div class="abs field" style="left:280px;top:862px;width:173px;height:55px">Question/Message</div>
<div class="abs field" style="left:96px;top:895px;width:173px;height:23px">Appointment Date*</div>
<div class="abs btn-send">SEND</div>

<h2 class="abs stories-title">Patient Stories</h2>
<div class="abs story" style="top:665px"><div class="story-img" role="img" aria-label="Patient portrait"></div><h3>Lorem Ipsum</h3><p>It is a long established fact that a reader will be distracted by the readable content of a page when looking at its layout.</p><span class="more">Read More</span></div>
<div class="abs story" style="top:742px"><div class="story-img" role="img" aria-label="Patient portrait"></div><h3>Lorem Ipsum</h3><p>It is a long established fact that a reader will be distracted by the readable content of a page when looking at its layout.</p><span class="more">Read More</span></div>
<div class="abs story" style="top:818px"><div class="story-img" role="img" aria-label="Patient portrait"></div><h3>Lorem Ipsum</h3><p>It is a long established fact that a reader will be distracted by the readable content of a page when looking at its layout.</p><span class="more">Read More</span></div>
<div class="abs story" style="top:894px"><div class="story-img" role="img" aria-label="Patient portrait"></div><h3>Lorem Ipsum</h3><p>It is a long established fact that a reader will be distracted by the readable content of a page when looking at its layout.</p><span class="more">Read More</span></div>

<footer>
  <h4 class="abs foot-h" style="left:92px">Quick Links</h4>
  <h4 class="abs foot-h" style="left:233px">Services</h4>
  <h4 class="abs foot-h" style="left:398px">Patient Info</h4>
  <ul class="abs foot-list" style="left:93px"><li>About</li><li>Services</li><li>Resources</li><li>Case Studies</li><li>Blog</li><li>Locate Us</li><li>Contact</li></ul>
  <ul class="abs foot-list" style="left:231px"><li>Cosmetic</li><li>Restorative</li><li>Tooth Replacement</li></ul>
  <ul class="abs foot-list" style="left:394px"><li>Mouth-Body Connection</li><li>Books &amp; Articles</li><li>FAQs</li><li>Helpful Links</li><li>Payment and Insurance</li><li>Pre &amp; Post Op Instructions</li></ul>
  <div class="abs foot-brand">Colin Ashford, DDS</div>
  <address class="abs foot-addr" style="font-style:normal">42 Harbor Lane<br>Suite 2 B<br>Westfield, WF 20417<br>Get Directions Tel: 123-555-0192</address>
  <div class="abs foot-rule"></div>
  <div class="abs copy">© Copyrights 2014 All rights Reserved</div>
</footer>
</body>
</html>
```